Online training business needs new website

We need a new wordpress website as a result of a rebranding. The business is a crisis management training company focussed on online training and simulation exercises. We only need a 4 page site - home, about us, contact us and blog. However we must be able to add additional tabs in the header to redirect to our sales and marketing system (Kartra). As these change from time to time, we must be able to add and delete as required.The site must be editable by us, with a basic understanding of wordpress and no understanding of coding. We don't want to have to employ someone to change text, add posts or add a new workshops etc. The theme chosen must be easy to edit by a beginner.

Target Market(s)

Senior managers food and consumer goods companies

Industry/Entity Type

Consulting

Coding

Coded - Design and coding required

Font styles to use
Sans Serif

Requirements
Must have
• Home page, about us, contact us, blog
• Colour scheme from logo (attached) - maroon, blue and grey
• If you go to the current website "tidewellcollege.com" and click on the "workshops" tab you will see the content I need on the home page for the plumvantage.com site
Nice to have
• Modern, simple and minimalist design is preferred

```html
<!DOCTYPE html>
<html lang="en">
<head>
<meta charset="utf-8">
<title>About Us – Plum Vantage</title>
<link href="https://fonts.googleapis.com/css2?family=Roboto:wght@400;500;700&family=Open+Sans:wght@400&display=swap" rel="stylesheet">
<style>
  :root {
    --navy: #0b3767;
    --maroon: #7d0f3d;
    --grey: #5a5a5a;
    --white: #ffffff;
    --hero-dark: #2a231d;
    --hero-mid: #5a4634;
  }
  * { box-sizing: border-box; margin: 0; padding: 0; }
  html, body { width: 719px; height: 1200px; overflow: hidden; background: var(--white); }
  body { position: relative; font-family: "Roboto", Arial, sans-serif; color: var(--navy); }

  .site-header { position: absolute; top: 0; left: 0; width: 719px; height: 67px; background: var(--white); z-index: 3; }
  .brand { position: absolute; left: 98px; top: 6px; width: 118px; height: 78px; background: var(--white); border-radius: 0 0 50px 50px; display: flex; align-items: center; gap: 6px; padding-left: 6px; }
  .brand-dot { width: 18px; height: 18px; border-radius: 50%; background: var(--maroon); flex: none; }
  .brand-name { font-size: 14px; font-weight: 700; color: var(--maroon); line-height: 1.05; letter-spacing: .5px; }
  .next-workshop { position: absolute; left: 376px; top: 14px; font-size: 8.5px; font-weight: 700; letter-spacing: .2px; }
  .register-btn { position: absolute; left: 558px; top: 8px; width: 63px; height: 22px; border-radius: 11px; background: var(--navy); color: var(--white); font-size: 8.5px; font-weight: 700; display: flex; align-items: center; justify-content: center; }
  .main-nav { position: absolute; left: 223px; top: 39px; display: flex; gap: 13px; font-size: 10.5px; }
  .main-nav a { color: var(--navy); text-decoration: none; }
  .main-nav a.current { color: var(--maroon); }

  .hero { position: absolute; top: 67px; left: 0; width: 719px; height: 258px; overflow: hidden; }
  .hero-photo { position: absolute; inset: 0; background: radial-gradient(ellipse at 45% 55%, var(--hero-mid) 0%, var(--hero-dark) 70%); }
  .hero-title { position: absolute; top: 92px; width: 100%; text-align: center; color: var(--white); font-size: 30px; font-weight: 700; }
  .hero-curve { position: absolute; left: 0; bottom: 0; }

  .about { position: absolute; top: 338px; left: 0; width: 719px; }
  .about-photo { position: absolute; left: 87px; top: 2px; width: 190px; height: 190px; border-radius: 50%; background: var(--navy); overflow: hidden; }
  .about-photo span { position: absolute; left: 12px; top: 10px; width: 170px; height: 170px; border-radius: 50%; background: linear-gradient(135deg, #e9e4df, #b9aea4); }
  .about-title { position: absolute; left: 290px; top: 10px; font-size: 21px; font-weight: 400; color: var(--navy); }
  .about-title em { font-style: normal; color: var(--maroon); }
  .about-text { position: absolute; left: 290px; top: 44px; width: 340px; font-family: "Open Sans", Arial, sans-serif; font-size: 9.4px; line-height: 18.5px; color: var(--grey); }
  .about-text p + p { margin-top: 18.5px; }

  .reach { position: absolute; top: 600px; left: 0; width: 719px; height: 510px; }
  .reach-bg { position: absolute; inset: 0; }
  .reach-heading { position: absolute; top: 56px; left: 130px; width: 460px; text-align: center; color: var(--white); font-size: 15px; font-weight: 700; line-height: 22px; }
  .enquire-btn { position: absolute; top: 132px; left: 311px; width: 110px; height: 34px; border-radius: 17px; background: var(--maroon); color: var(--white); font-size: 11.5px; font-weight: 700; display: flex; align-items: center; justify-content: center; }
  .world-map { position: absolute; top: 190px; left: 92px; width: 533px; height: 268px; border-radius: 40px; background: radial-gradient(ellipse at center, rgba(255,255,255,.22) 0%, rgba(255,255,255,.08) 70%, rgba(255,255,255,0) 100%); }

  .site-footer { position: absolute; top: 1134px; left: 0; width: 719px; text-align: center; }
  .footer-nav { display: flex; justify-content: center; gap: 13px; font-size: 10.5px; }
  .footer-nav a { color: var(--navy); text-decoration: none; }
  .copyright { margin-top: 8px; font-size: 10px; color: var(--grey); }
</style>
</head>
<body>
  <header class="site-header">
    <div class="brand"><span class="brand-dot"></span><span class="brand-name">PLUM<br>VANTAGE</span></div>
    <div class="next-workshop">NEXT WORK SHOP -&nbsp; SYDNEY , MELBOURNE</div>
    <div class="register-btn">REGISTER</div>
    <nav class="main-nav">
      <a class="current" href="#">ABOUT US</a><a href="#">WORKSHOPS</a><a href="#">ONLINE COURSE</a><a href="#">SIMULATIONS</a><a href="#">CONTACT US</a><a href="#">BLOG</a>
    </nav>
  </header>

  <section class="hero">
    <div class="hero-photo" role="img" aria-label="Hand stopping a row of falling wooden dominoes"></div>
    <h1 class="hero-title">ABOUT US</h1>
    <svg class="hero-curve" width="719" height="80" viewBox="0 0 719 80">
      <path d="M0,80 L0,78 Q360,0 719,78 L719,80 Z" fill="#ffffff"/>
      <path d="M65,72 Q360,10 650,68" fill="none" stroke="#0b3767" stroke-width="3"/>
      <circle cx="359" cy="30" r="21" fill="#ffffff"/>
    </svg>
  </section>

  <section class="about">
    <div class="about-photo" role="img" aria-label="Businesswoman speaking at a meeting table"><span></span></div>
    <h2 class="about-title"><em>ABOUT</em> PLUM VANTAGE</h2>
    <div class="about-text">
      <p>Donec convallis pede venenatis nibh Duis quam Nam eget lacus Aliquam erat volutpat Quisque dignissim congue leoMauris vel lacus vitae felis vestibulum volutpat Etiam est nunc venenatis in tristique eu imperdiet ac nisl Cum sociis natoque penatibus et magnis dis parturient montes nascetur ridiculus mus In iaculis facilisis massa Etiam eu urna Sed porta</p>
      <p>Suspendisse quam leo molestie sed luctus quis feugiat in pede Fusce tellus Sed metus augue convallis et vehicula ut pulvinar eu ante Integer orci tellus tristique vitae consequat nec porta vel lectus Nulla sit amet diam Duis non nunc Nulla rhoncus dictum metus Curabitur tristique mi condim</p>
    </div>
  </section>

  <section class="reach">
    <svg class="reach-bg" width="719" height="510" viewBox="0 0 719 510">
      <path d="M0,38 Q300,-10 560,12 Q380,8 0,58 Z" fill="#7d0f3d"/>
      <path d="M0,58 Q360,-10 719,48 L719,460 Q420,510 0,450 Z" fill="#0b3767"/>
      <path d="M719,460 Q560,496 360,498 Q560,505 719,477 Z" fill="#7d0f3d"/>
    </svg>
    <h2 class="reach-heading">THROUGH OUR PARTNERSHIP WITH MERIDEL INC AND MERIDEL GROUP, WE CAN DELIVER SERVICES IN MANY AREAS OF THE WORLD USING EXPERIENCED LOCAL CONSULTANTS.</h2>
    <div class="enquire-btn">ENQUIRE NOW</div>
    <div class="world-map" role="img" aria-label="Dotted world map marking consultant locations"></div>
  </section>

  <footer class="site-footer">
    <nav class="footer-nav">
      <a href="#">ABOUT US</a><a href="#">WORKSHOPS</a><a href="#">ONLINE COURSE</a><a href="#">SIMULATIONS</a><a href="#">CONTACT US</a><a href="#">BLOG</a>
    </nav>
    <p class="copyright">© 2019 Company Name&nbsp; All right reserved</p>
  </footer>
</body>
</html>
```